FunBrixo Business Card

We need a business card design for our company. We sell construction-themed amusement rides for kids.

Contact Information for Business Card

Contact info on business card should include:
Carl Dunning
Co-Founder & COO
(833) 571-FUNBRIX
Carl@funbrixo-demo.com
www.funbrixo-demo.com

```html
<!DOCTYPE html>
<html lang="en">
<head>
<meta charset="utf-8">
<title>FunBrixo Business Card</title>
<link rel="stylesheet" href="https://fonts.googleapis.com/css2?family=Oswald:wght@400;500;700&display=swap">
<style>
  :root {
    --card-dark: #1c1d1f;
    --panel-light: #eef2f6;
    --panel-blue: #dfe9f3;
    --orange: #e8772a;
    --blue: #2aa8e0;
    --pink: #e7268a;
    --purple: #7b3a96;
    --yellow: #f4b21b;
    --white: #ffffff;
    --text-light: #f2f2f2;
    --page: #ecebe8;
  }
  * { margin: 0; padding: 0; box-sizing: border-box; }
  html, body {
    width: 1125px; height: 1200px; overflow: hidden;
    background: var(--page);
    font-family: "Oswald", sans-serif;
  }
  .canvas { position: relative; width: 1125px; height: 1200px; }
  .card {
    position: absolute; left: 152px; width: 823px; height: 470px;
    border-radius: 22px; overflow: hidden;
    background: var(--card-dark);
    box-shadow: 0 6px 14px rgba(0,0,0,0.25);
  }
  .card-front { top: 99px; }
  .card-back { top: 631px; }

  /* front */
  .art-panel { position: absolute; inset: 0; width: 823px; height: 470px; }
  .brand-name {
    position: absolute; font-weight: 700; color: var(--orange);
    line-height: 1; white-space: nowrap; transform: translate(-50%, -50%);
  }
  .card-front .brand-name { left: 612px; top: 240px; font-size: 72px; }
  .person { position: absolute; left: 60px; top: 122px; }
  .person-name {
    font-size: 52px; font-weight: 500; line-height: 1; letter-spacing: 1px;
    text-transform: uppercase;
  }
  .c-orange { color: var(--orange); }
  .c-blue { color: var(--blue); }
  .c-pink { color: var(--pink); }
  .c-purple { color: var(--purple); }
  .c-yellow { color: var(--yellow); }
  .person-title {
    margin-top: 8px; font-size: 21px; font-weight: 400; color: var(--orange);
    letter-spacing: 2px; text-transform: uppercase;
  }
  .contact-list { position: absolute; left: 60px; top: 250px; list-style: none; }
  .contact-item {
    display: flex; align-items: center; gap: 10px; height: 28px;
    font-size: 18px; color: var(--text-light); letter-spacing: 0.5px; text-transform: uppercase;
  }
  .contact-icon { width: 18px; height: 18px; fill: var(--orange); }

  /* back */
  .card-back .brand-name { left: 412px; top: 222px; font-size: 96px; }
  .web-band {
    position: absolute; left: 0; top: 396px; width: 823px; height: 50px;
    background: var(--orange);
    display: flex; align-items: center; justify-content: center;
  }
  .web-band::before, .web-band::after {
    content: ""; position: absolute; left: 0; right: 0;
    border-top: 1px dashed rgba(255,255,255,0.8);
  }
  .web-band::before { top: 4px; }
  .web-band::after { bottom: 4px; }
  .web-address {
    font-size: 19px; font-weight: 700; color: var(--card-dark);
    letter-spacing: 5px; text-transform: uppercase; margin-left: -40px;
  }
  .band-edge {
    position: absolute; left: 0; top: 446px; width: 823px; height: 3px; background: var(--white);
  }
  .crew-illustration {
    position: absolute; left: 652px; top: 348px; width: 130px; height: 112px;
    border-radius: 14px;
    background: linear-gradient(180deg, #f3c21d 0%, #f3c21d 22%, #d9a58a 23%, #3c5a8a 100%);
  }
</style>
</head>
<body>
<main class="canvas">

  <section class="card card-front">
    <svg class="art-panel" viewBox="0 0 823 470" role="img" aria-label="Faint mascot illustration of a smiling builder in a hard hat">
      <defs>
        <linearGradient id="panelFade" x1="0" y1="0" x2="0" y2="1">
          <stop offset="0" stop-color="#f4f1ec"/>
          <stop offset="1" stop-color="#dfe9f3"/>
        </linearGradient>
      </defs>
      <path d="M395 0 L823 0 L823 470 L277 470 C276 420 292 380 322 362 C302 322 334 262 402 256 C404 200 388 100 395 0 Z" fill="url(#panelFade)"/>
    </svg>
    <div class="brand-name">FunBrixo</div>

    <div class="person">
      <h1 class="person-name"><span class="c-orange">C</span><span class="c-blue">a</span><span class="c-pink">r</span><span class="c-purple">l</span> <span class="c-yellow">D</span><span class="c-orange">u</span><span class="c-blue">n</span><span class="c-pink">n</span><span class="c-purple">i</span><span class="c-yellow">n</span><span class="c-orange">g</span></h1>
      <p class="person-title">Co-Founder &amp; COO</p>
    </div>

    <ul class="contact-list">
      <li class="contact-item">
        <svg class="contact-icon" viewBox="0 0 24 24" aria-hidden="true"><path d="M6.6 10.8a15.1 15.1 0 0 0 6.6 6.6l2.2-2.2a1 1 0 0 1 1-.25 11.4 11.4 0 0 0 3.6.57 1 1 0 0 1 1 1V20a1 1 0 0 1-1 1A17 17 0 0 1 3 4a1 1 0 0 1 1-1h3.5a1 1 0 0 1 1 1c0 1.25.2 2.45.57 3.57a1 1 0 0 1-.25 1z"/></svg>
        (833) 571-FUNBRIX
      </li>
      <li class="contact-item">
        <svg class="contact-icon" viewBox="0 0 24 24" aria-hidden="true"><path d="M2 5h20v14H2z M3 6l9 7 9-7" fill="var(--orange)"/><path d="M3 6.5l9 6.5 9-6.5" fill="none" stroke="#1c1d1f" stroke-width="1.6"/></svg>
        Carl@funbrixo-demo.com
      </li>
      <li class="contact-item">
        <svg class="contact-icon" viewBox="0 0 24 24" aria-hidden="true"><circle cx="12" cy="12" r="10"/><path d="M7 8c2 0 3 1 3 3s-2 2-2 4M14 5c0 2 2 3 4 3M15 19c0-2 1-3 3-3" fill="none" stroke="#1c1d1f" stroke-width="1.8"/></svg>
        funbrixo-demo.com
      </li>
    </ul>
  </section>

  <section class="card card-back">
    <div class="brand-name">FunBrixo</div>
    <div class="web-band">
      <span class="web-address">www.funbrixo-demo.com</span>
    </div>
    <div class="band-edge"></div>
    <div class="crew-illustration" role="img" aria-label="Illustration of two cartoon builders in yellow hard hats"></div>
  </section>

</main>
</body>
</html>
```